Webinar email campaign graphic/template

We need a static email campaign graphic that can be customized for a variety of communications - webinar announcement, whitepaper distribution, etc. Need ability to edit the files for text content. Attached are current examples/format. Please refer to website for design theme/ideas. www.korvelbillpath.com

Target Market(s)

Transportation executives

Industry/Entity Type

All

Requirements
Must have
• Ability to customize text for headers/content
Should not have
• Inability to edit text

```html
<!DOCTYPE html>
<html lang="en">
<head>
<meta charset="utf-8">
<title>Best Practices for Procuring a Freight Payment Solution – Korvel Billpath</title>
<link rel="stylesheet" href="https://fonts.googleapis.com/css2?family=Archivo:ital,wght@1,800;1,900&family=Roboto+Condensed:ital,wght@1,300;1,400&family=Roboto:wght@400;700;900&display=swap">
<style>
  :root {
    --navy: #003a78;
    --navy-line: #1d4a86;
    --orange: #e86d14;
    --ink: #111418;
    --grey-rule: #55606a;
    --white: #ffffff;
    --photo-top: #f4eef0;
    --photo-mid: #b5a9b6;
    --photo-low: #8a8e98;
  }
  * { box-sizing: border-box; margin: 0; padding: 0; }
  html, body { width: 1200px; height: 900px; overflow: hidden; background: var(--white); }
  .campaign {
    position: relative;
    width: 1200px;
    height: 900px;
    background: var(--white);
    font-family: "Roboto Condensed", "Arial Narrow", sans-serif;
    color: var(--ink);
  }

  .brand {
    position: absolute;
    left: 28px;
    top: 38px;
    display: flex;
    align-items: center;
    gap: 12px;
  }
  .brand-dot {
    width: 50px; height: 50px;
    border-radius: 50%;
    background: var(--navy);
  }
  .brand-name {
    font-family: "Roboto", Arial, sans-serif;
    font-weight: 400;
    font-size: 32px;
    color: #3c3f44;
    letter-spacing: -0.5px;
  }

  .hero-art { position: absolute; left: 0; top: 0; width: 1200px; height: 420px; }

  .headline {
    position: absolute;
    left: 440px;
    top: 34px;
    width: 690px;
    font-family: "Archivo", "Arial Black", sans-serif;
    font-weight: 900;
    font-style: italic;
    font-size: 80px;
    line-height: 100px;
    color: var(--white);
    letter-spacing: -1px;
    white-space: nowrap;
  }
  .subhead {
    position: absolute;
    right: 28px;
    top: 152px;
    font-family: "Archivo", "Arial Black", sans-serif;
    font-weight: 800;
    font-style: italic;
    font-size: 37px;
    color: var(--navy);
    white-space: nowrap;
  }

  .body-copy {
    position: absolute;
    left: 42px;
    top: 436px;
    width: 1130px;
    font-style: italic;
    font-weight: 400;
    font-size: 25.5px;
    line-height: 31.6px;
    letter-spacing: -0.2px;
  }
  .body-copy p + ul, .body-copy ul + p { margin-top: 31.6px; }
  .body-copy ul { list-style: none; padding-left: 30px; }
  .body-copy li { position: relative; }
  .body-copy li::before {
    content: "";
    position: absolute;
    left: -22px;
    top: 12px;
    width: 10px; height: 10px;
    border-radius: 50%;
    background: var(--ink);
  }

  .event-when { position: absolute; left: 42px; top: 794px; }
  .event-date {
    font-family: "Roboto", Arial, sans-serif;
    font-weight: 700;
    font-size: 30px;
    color: var(--navy);
    line-height: 36px;
  }
  .event-times {
    margin-top: 4px;
    font-style: italic;
    font-weight: 400;
    font-size: 22px;
    letter-spacing: -0.3px;
  }
  .event-times .sep { display: inline-block; width: 2px; height: 24px; background: var(--ink); margin: 0 6px; vertical-align: -4px; }

  .rule { position: absolute; top: 868px; height: 2px; background: var(--navy-line); }
  .rule-left { left: 0; width: 410px; }
  .rule-right { left: 786px; width: 414px; }

  .register {
    position: absolute;
    left: 434px; top: 778px;
    width: 332px; height: 106px;
    border: 3px solid var(--orange);
    border-radius: 42px;
    padding: 4px;
    background: var(--white);
  }
  .register-face {
    width: 100%; height: 100%;
    border-radius: 36px;
    background: var(--orange);
    display: flex; align-items: center; justify-content: center;
    font-family: "Roboto", Arial, sans-serif;
    font-weight: 900;
    font-size: 47px;
    color: var(--white);
    letter-spacing: 0.5px;
    text-decoration: none;
  }

  .site-url {
    position: absolute;
    left: 783px; top: 812px;
    font-family: "Roboto", Arial, sans-serif;
    font-weight: 700;
    font-size: 29px;
    color: var(--navy);
    letter-spacing: 0.2px;
  }
</style>
</head>
<body>
<main class="campaign">
  <svg class="hero-art" viewBox="0 0 1200 420" aria-hidden="false">
    <defs>
      <linearGradient id="photoTone" x1="0" y1="0" x2="0" y2="1">
        <stop offset="0" stop-color="#ffffff"/>
        <stop offset="0.18" stop-color="var(--photo-top)"/>
        <stop offset="0.55" stop-color="var(--photo-mid)"/>
        <stop offset="1" stop-color="var(--photo-low)"/>
      </linearGradient>
      <linearGradient id="photoGlow" x1="0" y1="0" x2="1" y2="0">
        <stop offset="0" stop-color="#e8b48a" stop-opacity="0.35"/>
        <stop offset="0.3" stop-color="#f2c99a" stop-opacity="0.25"/>
        <stop offset="0.7" stop-color="#9ea6b4" stop-opacity="0.2"/>
        <stop offset="1" stop-color="#c8ccd4" stop-opacity="0.3"/>
      </linearGradient>
      <filter id="bandShadow" x="-5%" y="-20%" width="110%" height="150%">
        <feDropShadow dx="0" dy="4" stdDeviation="3" flood-color="#000" flood-opacity="0.45"/>
      </filter>
    </defs>
    <g role="img" aria-label="Photo of freight trucks on the highway at dusk with headlights on">
      <polygon points="0,198 1200,198 1200,292 600,408 0,292" fill="url(#photoTone)"/>
      <polygon points="0,240 1200,240 1200,292 600,408 0,292" fill="url(#photoGlow)"/>
    </g>
    <polyline points="0,292 600,406 1200,292" fill="none" stroke="var(--white)" stroke-width="3"/>
    <polyline points="0,298 600,410 1200,298" fill="none" stroke="var(--grey-rule)" stroke-width="4"/>
    <polygon points="377,29 1200,29 1200,139 377,139 358,84" fill="var(--navy)" filter="url(#bandShadow)"/>
  </svg>

  <div class="brand">
    <span class="brand-dot"></span>
    <span class="brand-name">Korvel Billpath</span>
  </div>

  <h1 class="headline">BEST PRACTICES</h1>
  <h2 class="subhead">for Procuring a Freight Payment Solution</h2>

  <section class="body-copy">
    <p>Lorem ipsum dolor sit amet, consectetuer adipiscing elit, sed diam nonummy nibh euismod tincidunt ut laoreet dolore magna aliquam erat volutpat. Ut wisi enim ad minim veniam, quis nostrud exerci tation</p>
    <ul>
      <li>ullamcorper suscipit lobortis nisl ut aliquip</li>
      <li>hendrerit in vulputate velit esse molestie</li>
      <li>accumsan et iusto odio dignissim</li>
    </ul>
    <p>Lorem ipsum dolor sit amet, cons ectetuer adipiscing elit, sed diam nonummy nibh euismod tincidunt ut laoreet dolore magna aliquam erat volutpat. Ut wisi enim ad minim veniam, quis nostrud exerci tation ullamcorper suscipit lobortis nisl ut aliquip ex ea commodo consequat.</p>
  </section>

  <div class="event-when">
    <p class="event-date">Wednesday, July 26, 2021</p>
    <p class="event-times">11:30 Eastern<span class="sep"></span>10:30 Central<span class="sep"></span>8:30 Pacific</p>
  </div>
  <div class="rule rule-left"></div>

  <div class="register"><a class="register-face" href="#">REGISTER</a></div>

  <p class="site-url">www.korvelbillpath.com</p>
  <div class="rule rule-right"></div>
</main>
</body>
</html>
```